RW Framewell Inc Business cards

We need business cards using our existing logo but slightly modified. Right now the logo says RW Loadbearing Masonry. We want to keep the RW part of the design, but replace the Structural Concrete portion with "FRAMEWELL". Please see the attached file.
Ideally this would be a blank template so we can add Different Names, titles, and phone numbers later.
On the one side we want only the logo and on the other side the detail. I'm attaching an example for you to see.
Please reach out with any other questions. Our address and other details will be given out once we find a design we like.

Target Market(s)

Construction Industry

```html
<!DOCTYPE html>
<html lang="en">
<head>
<meta charset="utf-8">
<title>RW Framewell Inc – Business Cards</title>
<link href="https://fonts.googleapis.com/css2?family=Roboto:wght@400;700&display=swap" rel="stylesheet">
<style>
  :root {
    --backdrop: #5d80b9;
    --brand-blue: #2f63a6;
    --brand-blue-deep: #24528f;
    --card-white: #f4f4f3;
    --ink-grey: #555a60;
    --edge-grey: #7a7c80;
    --white: #ffffff;
  }
  * { box-sizing: border-box; margin: 0; padding: 0; }
  html, body { width: 1200px; height: 852px; overflow: hidden; }
  body {
    background: var(--backdrop);
    font-family: "Roboto", Arial, sans-serif;
    position: relative;
  }
  .card {
    position: absolute;
    top: 256px;
    width: 520px;
    height: 320px;
    border-radius: 26px;
    overflow: hidden;
  }
  .card--front { left: 50px; background: var(--brand-blue); }
  .card--back { left: 630px; background: var(--card-white); }

  .wordmark {
    position: absolute;
    font-family: "Roboto", Arial, sans-serif;
    font-weight: 700;
    line-height: 1;
    text-align: center;
  }
  .wordmark__initials { display: block; font-size: 96px; letter-spacing: 2px; }
  .wordmark__name { display: block; font-size: 30px; letter-spacing: 8px; margin-top: 4px; }

  .card--front .wordmark {
    left: 0; right: 0; top: 92px;
    color: var(--brand-blue-deep);
  }
  .card--back .wordmark {
    left: 34px; top: 112px; width: 220px;
    color: var(--brand-blue);
  }
  .card--back .wordmark__initials { font-size: 72px; }
  .card--back .wordmark__name { font-size: 22px; letter-spacing: 5px; }

  .details {
    position: absolute;
    left: 286px; top: 40px;
    color: var(--ink-grey);
  }
  .details__name { font-size: 21px; font-weight: 700; color: var(--brand-blue); }
  .details__title { font-size: 13px; margin-top: 2px; }
  .contact { list-style: none; margin-top: 22px; }
  .contact li {
    display: flex; align-items: flex-start; gap: 10px;
    font-size: 13px; line-height: 1.35; margin-bottom: 6px;
  }
  .contact svg { flex: none; width: 13px; height: 13px; margin-top: 2px; fill: var(--brand-blue); }

  .tagline-tab {
    position: absolute;
    right: 0; bottom: 0;
    width: 258px; height: 50px;
    background: var(--brand-blue);
    border-top-left-radius: 22px;
    color: var(--white);
    font-size: 14px; font-weight: 700;
    display: flex; align-items: center; justify-content: center;
  }
  .base-strip {
    position: absolute;
    left: 0; bottom: 0;
    width: 262px; height: 8px;
    background: var(--edge-grey);
  }
</style>
</head>
<body>
  <section class="card card--front" aria-label="Card front">
    <div class="wordmark">
      <span class="wordmark__initials">RW</span>
      <span class="wordmark__name">FRAMEWELL</span>
    </div>
  </section>

  <section class="card card--back" aria-label="Card back">
    <div class="wordmark">
      <span class="wordmark__initials">RW</span>
      <span class="wordmark__name">FRAMEWELL</span>
    </div>

    <div class="details">
      <p class="details__name">Dale RW Porter</p>
      <p class="details__title">Managing Director</p>
      <ul class="contact">
        <li>
          <svg viewBox="0 0 24 24"><path d="M6.6 10.8a15 15 0 0 0 6.6 6.6l2.2-2.2a1 1 0 0 1 1-.25 11.4 11.4 0 0 0 3.6.57 1 1 0 0 1 1 1V20a1 1 0 0 1-1 1A17 17 0 0 1 3 4a1 1 0 0 1 1-1h3.5a1 1 0 0 1 1 1c0 1.25.2 2.45.57 3.57a1 1 0 0 1-.25 1z"/></svg>
          <span>555-014-2290</span>
        </li>
        <li>
          <svg viewBox="0 0 24 24"><path d="M2 5h20v14H2z M2 5l10 8 10-8" fill="none" stroke="#2f63a6" stroke-width="2.4"/></svg>
          <span>dale@framewellco.com</span>
        </li>
        <li>
          <svg viewBox="0 0 24 24"><circle cx="12" cy="12" r="9" fill="none" stroke="#2f63a6" stroke-width="2.2"/><path d="M3 12h18M12 3c3 3 3 15 0 18M12 3c-3 3-3 15 0 18" fill="none" stroke="#2f63a6" stroke-width="1.8"/></svg>
          <span>www.framewellco.com</span>
        </li>
        <li>
          <svg viewBox="0 0 24 24"><path d="M12 2a7 7 0 0 0-7 7c0 5 7 13 7 13s7-8 7-13a7 7 0 0 0-7-7zm0 9.5A2.5 2.5 0 1 1 12 6.5a2.5 2.5 0 0 1 0 5z"/></svg>
          <span>58 Brickyard Rd., Millbrook,<br>Oregon, US 970112</span>
        </li>
      </ul>
    </div>

    <div class="base-strip"></div>
    <div class="tagline-tab">RW Loadbearing Masonry</div>
  </section>
</body>
</html>
```